Help design website for "Brightwater Civic Advisors" to advance the common good

Here is the Google doc link that lays out the design:

https://files.plumrivet.example/sheet/d/7QmTzR2wLx9KpVbN4hJcY8sEaUoFdG3iXkMnPq5rWt6/edit?usp=sharing

Here is the Google drive folder with the logos and photos: https://vault.plumrivet.example/open?id=4HkWp9LzQe2TxRvN8mBaYc3DsUoJfG6

The testimonials are being gathered and will be shared by Friday, 1/4.

The winner will also have to migrate the coding files to my hosting site.

Thank you for your help! Looking forward to seeing your designs.

Target Market(s)

Prospective clients

Industry/Entity Type

Non Profit

Coding

Coded - Design and coding required

Number of Pages Required

5+ page

Requirements
Must have
• Noted in the Google doc regarding layout.
Nice to have

```html
<!DOCTYPE html>
<html lang="en">
<head>
<meta charset="utf-8">
<title>Brightwater Civic Advisors — Services &amp; Testimonials</title>
<link href="https://fonts.googleapis.com/css2?family=Poppins:wght@400;600;700&family=Open+Sans:wght@400;700&display=swap" rel="stylesheet">
<style>
  :root {
    --brand-blue: #3a88cf;
    --ink: #222428;
    --body-text: #3a3a3a;
    --footer-bg: #25272f;
    --white: #ffffff;
    --band-bg: #f4f4f5;
    --card-shadow: rgba(0, 0, 0, 0.10);
  }
  * { box-sizing: border-box; margin: 0; padding: 0; }
  html, body { width: 748px; height: 1200px; overflow: hidden; background: var(--white); }
  body { position: relative; font-family: "Open Sans", Arial, sans-serif; color: var(--body-text); }

  /* Wordmark */
  .brand { position: absolute; display: flex; align-items: center; color: var(--white); }
  .brand-square { width: 34px; height: 34px; background: var(--white); margin-right: 12px; flex: none; }
  .brand-name { font-family: "Poppins", Arial, sans-serif; font-weight: 600; font-size: 17px; line-height: 1; white-space: nowrap; }

  /* Header */
  .site-header { position: absolute; top: 0; left: 0; width: 748px; height: 96px; background: var(--brand-blue); }
  .site-header .brand { left: 89px; top: 31px; }
  .cta { position: absolute; left: 458px; top: 18px; width: 200px; height: 31px; border: 2px solid var(--white); color: var(--white); font-family: "Poppins", Arial, sans-serif; font-weight: 600; font-size: 8.4px; display: flex; align-items: center; justify-content: center; text-decoration: none; text-transform: uppercase; }
  .main-nav { position: absolute; top: 69px; left: 367px; display: flex; gap: 13px; }
  .main-nav a { color: var(--white); font-family: "Poppins", Arial, sans-serif; font-weight: 600; font-size: 8.4px; text-transform: uppercase; text-decoration: none; }
  .main-nav a.is-current { text-decoration: underline; text-underline-offset: 2px; }

  /* Hero */
  .hero-photo { position: absolute; top: 96px; left: 0; width: 748px; height: 346px; background: linear-gradient(180deg, #5b5650 0%, #7c6a5e 40%, #3d3b3e 100%); }
  .hero-edge { position: absolute; top: 360px; left: 0; width: 748px; height: 84px; }

  /* Intro */
  .intro { position: absolute; top: 426px; left: 0; width: 748px; text-align: center; }
  .intro h1 { font-family: "Poppins", Arial, sans-serif; font-weight: 600; font-size: 16px; color: var(--ink); }
  .intro p { width: 420px; margin: 17px auto 0; font-size: 9.3px; line-height: 12.4px; color: var(--body-text); }

  /* Testimonial cards */
  .testimonial { position: absolute; top: 541px; width: 273px; height: 390px; background: var(--white); box-shadow: 0 2px 8px var(--card-shadow); }
  .testimonial--left { left: 89px; }
  .testimonial--right { left: 385px; }
  .testimonial-photo { position: relative; height: 222px; }
  .testimonial--left .testimonial-photo { background: linear-gradient(160deg, #6d5a48 0%, #8a7b6e 45%, #2b2a2e 100%); }
  .testimonial--right .testimonial-photo { background: linear-gradient(180deg, #a8a39d 0%, #8d857b 55%, #3c3633 100%); }
  .photo-caption { position: absolute; left: 18px; right: 16px; bottom: 13px; color: var(--white); font-family: "Poppins", Arial, sans-serif; font-weight: 600; font-size: 9.2px; line-height: 11.2px; text-transform: uppercase; }
  .quote { position: relative; padding: 36px 30px 0 31px; font-size: 8.2px; line-height: 11px; color: var(--body-text); }
  .quote-mark { font-family: Georgia, serif; font-weight: 700; font-size: 22px; color: var(--ink); line-height: 0; }
  .quote-mark--open { position: absolute; left: 17px; top: 38px; }
  .quote-mark--close { display: inline-block; margin-left: 8px; vertical-align: -10px; }
  .attribution { position: absolute; left: 33px; top: 348px; font-size: 8.2px; line-height: 11px; color: var(--body-text); }
  .attribution strong { font-weight: 700; color: var(--ink); }

  /* Footer */
  .footer-art { position: absolute; top: 956px; left: 0; width: 748px; height: 244px; }
  .site-footer { position: absolute; top: 1064px; left: 0; width: 748px; height: 136px; }
  .site-footer .brand { left: 90px; top: 40px; }
  .site-footer .brand-square { background: var(--brand-blue); }
  .footer-divider { position: absolute; left: 382px; top: 16px; width: 1px; height: 88px; background: #4a4c55; }
  .footer-menu { position: absolute; left: 419px; top: 26px; color: var(--white); }
  .footer-menu h2 { font-family: "Poppins", Arial, sans-serif; font-weight: 700; font-size: 7.4px; }
  .footer-links { display: flex; margin-top: 14px; font-size: 7px; }
  .footer-links a { color: var(--white); text-decoration: none; text-transform: uppercase; }
  .footer-links span { margin: 0 7px; }
  .copyright { position: absolute; left: 419px; top: 86px; font-size: 7px; color: var(--white); }
</style>
</head>
<body>
  <header class="site-header">
    <div class="brand">
      <div class="brand-square"></div>
      <div class="brand-name">Brightwater Civic Advisors</div>
    </div>
    <a class="cta" href="#">Book a complimentary consultation</a>
    <nav class="main-nav">
      <a href="#">About</a>
      <a href="#" class="is-current">Services &amp; Testimonials</a>
      <a href="#">Media &amp; Impact</a>
      <a href="#">Contact</a>
    </nav>
  </header>

  <div class="hero-photo" role="img" aria-label="Photo of Dana talking with guests at a university community engagement event"></div>
  <svg class="hero-edge" viewBox="0 0 748 84" preserveAspectRatio="none" aria-hidden="true">
    <polygon points="0,74 374,10 748,74 748,84 0,84" fill="var(--brand-blue)"/>
    <polygon points="0,80 374,17 748,80 748,84 0,84" fill="var(--white)"/>
    <rect x="0" y="80" width="748" height="4" fill="var(--white)"/>
  </svg>

  <section class="intro">
    <h1>Community Partnership Development</h1>
    <p>Dana has collaborated with more than 250 nonprofits, schools, government agencies, and businesses with corporate social responsibility units to create mutually beneficial partnerships. These relationships have been strengthened and sustained to expand programming and initiatives that meet community engagement outcomes.</p>
  </section>

  <article class="testimonial testimonial--left">
    <div class="testimonial-photo" role="img" aria-label="Photo of Dana with volunteers at a community garden">
      <p class="photo-caption">Dana with volunteers working at an Earth Day of Service community garden</p>
    </div>
    <blockquote class="quote">
      <span class="quote-mark quote-mark--open">&ldquo;</span>
      Dana has a unique ability to bring people and institutions together. Dana's ability to lead and expertly facilitate thoughtful and productive conversations has yielded tangible results that are demonstrated in the strong and lasting community partnerships she has helped create.<span class="quote-mark quote-mark--close">&rdquo;</span>
    </blockquote>
    <p class="attribution"><strong>Lorna Vesey,</strong> Executive Director,<br>Cedar Row Community Development</p>
  </article>

  <article class="testimonial testimonial--right">
    <div class="testimonial-photo" role="img" aria-label="Photo of Dana with a learning cohort in front of a large street sign">
      <p class="photo-caption">Dana with the Common Ground cohort learning about community and economic development in Chinatown</p>
    </div>
    <blockquote class="quote">
      <span class="quote-mark quote-mark--open">&ldquo;</span>
      Dana is a champion who has proven success for bridging the gap between community and higher education. She is committed, consistent, compassionate, and dedicated to civic engagement. Dana is also patient and persistent and values strong relationship-building.<span class="quote-mark quote-mark--close">&rdquo;</span>
    </blockquote>
    <p class="attribution"><strong>Tessa Moraine</strong> Chief Program Officer,<br>Riverbend Youth Programs</p>
  </article>

  <svg class="footer-art" viewBox="0 0 748 244" preserveAspectRatio="none">
    <rect x="0" y="0" width="748" height="108" fill="var(--band-bg)"/>
    <polygon points="0,108 374,44 748,108 748,244 0,244" fill="var(--footer-bg)"/>
  </svg>

  <footer class="site-footer">
    <div class="brand">
      <div class="brand-square"></div>
      <div class="brand-name">Brightwater Civic Advisors</div>
    </div>
    <div class="footer-divider"></div>
    <div class="footer-menu">
      <h2>MENU</h2>
      <nav class="footer-links">
        <a href="#">About</a><span>|</span>
        <a href="#">Services &amp; Testimonials</a><span>|</span>
        <a href="#">Media &amp; Impact</a><span>|</span>
        <a href="#">Contact</a>
      </nav>
    </div>
    <p class="copyright">Copyrights @ 2019 All Rights Reserved</p>
  </footer>
</body>
</html>
```